Investment Memorandum Document

IM for Harbourline Lending Fund - is the document that needs work

Make sure it is all done in MS WORD so that i or lawyers can edit some words if required

the IM is NOT final but its 95% of the way there. Maybe a few more pages and wording changes - but that is something i can do i guess or you can easier adjust

Just to typeset and pretty it all up - a few sample finished products have been uploaded for reference.

KTR IM is the one i like - but feel free to show off your skills

put 1.2 to 1.8 all in contrasting row tables

Target Market(s)

Individual and Institutional investors with money

Industry/Entity Type

Investment Banking

Colors

Designer to choose colors to be used in the design.

Requirements
Must have
• clear professional layout and easy on the eye
• https://www.filevaultexample.net/sh/84k3p77zrm2wqtn/BBDfpqWem3PvtsLxQZMUD41Lb?dl=0
• use the link above for high res images
Nice to have
• pictures and graphics
Should not have
• cartoons

```html
<!DOCTYPE html>
<html lang="en">
<head>
<meta charset="utf-8">
<title>Harbourline Lending Fund – Information Memorandum</title>
<link rel="stylesheet" href="https://fonts.googleapis.com/css2?family=Roboto:wght@300;400&display=swap">
<style>
  :root{
    --backdrop:#4a4a4a;
    --paper:#fbfbfa;
    --gold:#dba24a;
    --gold-soft:#fbf5ea;
    --ink:#6b6b6b;
    --band:#3b3b3b;
    --band-text:#f2f2f2;
  }
  *{box-sizing:border-box;margin:0;padding:0}
  html,body{width:1200px;height:774px;overflow:hidden;background:var(--backdrop);font-family:'Roboto',Arial,sans-serif;font-weight:300;color:var(--ink)}
  .page{position:absolute;top:114px;width:385px;height:544px;background:var(--paper)}
  .page-notice{left:200px}
  .page-features{left:614px}

  .notice-title{position:absolute;left:27px;top:45px;font-size:12.5px;font-weight:300;color:var(--gold)}
  .column{position:absolute;top:65px;width:156px;font-size:5.4px;line-height:8.55px;text-align:justify}
  .column-a{left:27px}
  .column-b{left:201px}
  .column p{text-indent:5px;margin-bottom:2px}
  .column h3{font-size:7px;font-weight:400;color:var(--gold);line-height:10px;margin:1px 0 3px 5px;text-align:justify;letter-spacing:.1px}

  .footer{position:absolute;top:511px;height:17px;font-size:5.8px;line-height:17px}
  .footer-band{background:var(--band);color:var(--band-text);width:77px;display:flex;align-items:center;gap:6px;padding-left:27px}
  .page-notice .footer-band{left:0;padding-left:28px}
  .page-features .footer-band{right:0;padding-left:7px;gap:7px}
  .footer-mark{display:inline-block;width:6px;height:6px;border-radius:50%;background:var(--gold)}
  .footer-title{white-space:nowrap}
  .page-notice .footer-title{right:27px}
  .page-features .footer-title{left:28px}

  .section-title{position:absolute;left:33px;top:53px;font-size:7.2px;font-weight:400;color:var(--gold)}
  .section-title span{margin-right:6px}
  .section-intro{position:absolute;left:28px;top:64px;width:332px;font-size:5.4px;line-height:8px;text-align:right}
  .features{position:absolute;left:28px;top:83px;width:330px;border-collapse:separate;border-spacing:0 1px;font-size:5.4px;line-height:7.6px}
  .features td{border-top:1px solid var(--gold);border-bottom:1px solid var(--gold);vertical-align:top;padding:6px 7px}
  .features td:first-child{border-left:1px solid var(--gold);border-right:1px solid var(--gold);width:84px;color:var(--gold);font-weight:400}
  .features td:last-child{border-right:1px solid var(--gold);padding-left:8px;padding-right:12px}
  .features .row-trustee td{height:30px}
  .features .row-manager td{height:46px;background:var(--gold-soft)}
</style>
</head>
<body>

<section class="page page-notice">
  <h1 class="notice-title">Notice</h1>

  <div class="column column-a">
    <p>This Information memorandum is dated XXX and is issued by Northgate Investment and Lending Corporation Pty Ltd ACN 152 604 377, holder of AFS licence number 418250, (Trustee), which is the trustee of the Diversified Commercial Income Fund (Fund).</p>
    <p>The purpose of this IM is to provide information for prospective investors to decide whether they wish to invest in the Fund.</p>
    <p>The Trustee has appointed Harbourline Asset Management Pty Ltd (Investment Manager) as the investment manager of the Fund under the Investment Management Agreement. The Investment Manager is an authorised representative (number 1284417XXX) of Northgate Investment and Lending Corporation Pty Ltd ACN 152 604 377 AFS licence number 418250. The purpose of this IM is to provide information for prospective Investors to decide whether they wish to invest in the Fund. The Fund’s trust deed (Trust Deed) provides for different Classes of Units. Under the Trust Deed, the different Classes of Units may have different rights and obligations. The performance of different Classes of Units may also differ depending on the investments of that Class. Holders of different Classes of Units will be treated fairly.</p>
    <h3>NO DISCLOSURE REQUIRED</h3>
    <p>This IM is intended to provide potential Investors with information only and does not constitute a product disclosure statement or other disclosure document required by the Corporations Act 2001 (Cth) (Act). This IM has not been lodged with the Australian Securities and Investments Commission (ASIC) or any other government body.</p>
    <p>The offer made under this IM is only available to persons who qualify as wholesale clients (as defined in section 761G (7) of the Corporations Act) or sophisticated investors (as defined in section 761GA of the Corporations Act). (collectively, Qualified Investors). The Trustee will not issue Units in the Fund to a person unless it is satisfied that the person is a Qualified Investor.</p>
    <h3>RESTRICTIONS ON DISTRIBUTION</h3>
    <p>This IM does not constitute, and may not be used for the purposes of, an offer of Units or an invitation to apply to participate in the Fund by any person in any jurisdiction in which such offer or invitation is not authorised or in which the person endeavouring to make such offer or invitation is not qualified to do so or to any person to whom it is unlawful to make such an offer or invitation.</p>
  </div>

  <div class="column column-b">
    <p>No action has been taken to register or qualify interests in the Fund, the invitation to participate in the Fund, or to otherwise permit any public offering of Fund interests in any jurisdiction other than Australia. It is the responsibility of prospective Investors to satisfy themselves as to full compliance with the relevant laws and regulations of any jurisdiction in connection with any application to participate in the Fund, including obtaining any requisite governmental or other consent and adhering to any other formality prescribed in such jurisdiction.</p>
    <p>By receiving and viewing this IM, the recipient is warranting that they are legally entitled to do so and the securities laws of their relevant jurisdiction do no prohibit them from acquiring interests in the Fund. Further, the persons receiving and viewing this IM warrant that they are Qualified Investors.</p>
    <p>In particular, this product has not been and will not be registered under the US Securities Act or the securities laws of any state of the United States and may not be offered, sold, delivered or transferred in the United States or to, or for the account of, any “US Person” (as defined in Regulation S under the US Securities Act). Neither this IM, Application Form or other material relating to this product may be distributed in the United States. With respect to Australian jurisdiction, this IM have been prepared on the basis that the prospective Investors are wholesale clients or sophisticated investors, not retail clients within the meaning of the Corporations Act. Accordingly, this IM is not a product disclosure statement and does not contain all of the information that would be included in a product disclosure statement issued under the Corporations Act.</p>
    <p>The Trustee may in the future take actions to offer interests in the Fund in other jurisdictions.</p>
    <h3>NO RESPONSIBILITY FOR CONTENTS OF DOCUMENT</h3>
    <p>To the maximum extent permitted by law, none of the Trustee, the Investment Manager, or any of their associates, related parties, directors, officers, employees, advisors (including financial, accounting and legal advisors) or representatives make any recommendation in relation to the Fund, or make any representation or warranty, express or implied, as to the accuracy, reliability or completeness of the information contained in this IM.</p>
    <p>This IM does not purport to contain all the information that a prospective Investor may require in evaluating a possible investment in the Fund.</p>
  </div>

  <div class="footer footer-band"><span>Page 3</span><span class="footer-mark"></span></div>
  <div class="footer footer-title">Harbourline Diversified Commercial Income Fund – Information Memorandum</div>
</section>

<section class="page page-features">
  <h2 class="section-title"><span>1.2</span>Key Features</h2>
  <p class="section-intro">The table below is only a summary of the key features of an investment in the Fund. It is not intended to be exhaustive. You must read the whole of this IM to obtain more detailed information before making a decision to invest in the Fund.</p>

  <table class="features">
    <tr class="row-trustee"><td>Trustee</td><td>Northgate Investment and Lending Corporation Pty Ltd is the trustee of the Fund and will be responsible for holding title to the Fund’s assets.</td></tr>
    <tr class="row-manager"><td>Investment Manager</td><td>Harbourline Asset Management Pty Ltd has been appointed as the investment manager of the Fund and is responsible for managing the Fund’s assets. The Investment Manager will source and assess potential loans for the Fund and will monitor the day-to-day management of the Fund’s loans.</td></tr>
    <tr class="row-trustee"><td>Trustee</td><td>Northgate Investment and Lending Corporation Pty Ltd is the trustee of the Fund and will be responsible for holding title to the Fund’s assets.</td></tr>
    <tr class="row-manager"><td>Investment Manager</td><td>Harbourline Asset Management Pty Ltd has been appointed as the investment manager of the Fund and is responsible for managing the Fund’s assets. The Investment Manager will source and assess potential loans for the Fund and will monitor the day-to-day management of the Fund’s loans.</td></tr>
    <tr class="row-trustee"><td>Trustee</td><td>Northgate Investment and Lending Corporation Pty Ltd is the trustee of the Fund and will be responsible for holding title to the Fund’s assets.</td></tr>
    <tr class="row-manager"><td>Investment Manager</td><td>Harbourline Asset Management Pty Ltd has been appointed as the investment manager of the Fund and is responsible for managing the Fund’s assets. The Investment Manager will source and assess potential loans for the Fund and will monitor the day-to-day management of the Fund’s loans.</td></tr>
    <tr class="row-trustee"><td>Trustee</td><td>Northgate Investment and Lending Corporation Pty Ltd is the trustee of the Fund and will be responsible for holding title to the Fund’s assets.</td></tr>
    <tr class="row-manager"><td>Investment Manager</td><td>Harbourline Asset Management Pty Ltd has been appointed as the investment manager of the Fund and is responsible for managing the Fund’s assets. The Investment Manager will source and assess potential loans for the Fund and will monitor the day-to-day management of the Fund’s loans.</td></tr>
    <tr class="row-trustee"><td>Trustee</td><td>Northgate Investment and Lending Corporation Pty Ltd is the trustee of the Fund and will be responsible for holding title to the Fund’s assets.</td></tr>
    <tr class="row-manager"><td>Investment Manager</td><td>Harbourline Asset Management Pty Ltd has been appointed as the investment manager of the Fund and is responsible for managing the Fund’s assets. The Investment Manager will source and assess potential loans for the Fund and will monitor the day-to-day management of the Fund’s loans.</td></tr>
  </table>

  <div class="footer footer-title">Harbourline Diversified Commercial Income Fund – Information Memorandum</div>
  <div class="footer footer-band"><span class="footer-mark"></span><span>Page 2</span></div>
</section>

</body>
</html>
```